Business Card for a Jewellery Brand

Business card for an upscale jewellery brand. Attached is the brand logo and icon and color board. I am looking for two card versions: one for the founder and one is generic. The card should be elegant and convey upscale and premium feel. I am open to both square and rectangle card shapes.

Industry/Entity Type

Jewelry

Contact Information for Business Card

Two cards: (1) Sunela Parvaniya (Founder) (2) General
(1) Sunela Parvaniya card should have Name: Sunela Parvaniya, Title: Founder Email id: sunela@quiremo.com.au. Phone no: +61452913307
(2) Generic card should have Email id: info@quiremo.com.au. Phone no: +61436207518

Requirements
Must have
• Workmark
• ICON
• Phone no
• Email ID
• ABN: 58219740312 (Note: ABN is Business number in Australia)
• Website: www.quiremo.com.au
• Instagram: quiremo_jewellery
• Facebook: @quiremojewellery
Nice to have
• Tagline

```html
<!DOCTYPE html>
<html lang="en">
<head>
<meta charset="utf-8">
<title>Quiremo Business Cards</title>
<link href="https://fonts.googleapis.com/css2?family=Montserrat:wght@400;600&family=Open+Sans:wght@400&display=swap" rel="stylesheet">
<style>
  :root {
    --blush: #e5938f;
    --white: #ffffff;
    --backdrop: #ece8e6;
  }
  html, body {
    margin: 0;
    width: 1200px;
    height: 900px;
    overflow: hidden;
    background: var(--backdrop);
  }
  .canvas {
    position: relative;
    width: 1200px;
    height: 900px;
  }
  .card {
    position: absolute;
    background: var(--white);
    overflow: hidden;
    box-shadow: 0 6px 18px rgba(0,0,0,0.12);
  }
  .card--founder {
    left: 78px;
    top: 34px;
    width: 588px;
    height: 364px;
  }
  .card--brand {
    left: 388px;
    top: 505px;
    width: 566px;
    height: 352px;
  }
  .founder-panel {
    position: absolute;
    inset: 0;
  }
  .founder-details {
    position: absolute;
    left: 32px;
    top: 48px;
    color: var(--white);
    font-family: "Open Sans", sans-serif;
  }
  .founder-name {
    margin: 0;
    font-family: "Montserrat", sans-serif;
    font-weight: 600;
    font-size: 19px;
    letter-spacing: 0.3px;
    text-transform: uppercase;
  }
  .founder-title {
    margin: 2px 0 0;
    font-size: 14px;
  }
  .founder-abn {
    margin: 16px 0 0;
    font-size: 14px;
  }
  .contact-list {
    list-style: none;
    margin: 0;
    padding: 0;
    position: absolute;
    left: 32px;
    top: 192px;
    color: var(--white);
    font-family: "Open Sans", sans-serif;
    font-size: 14px;
  }
  .contact-list li {
    display: flex;
    align-items: center;
    gap: 6px;
    height: 21.5px;
  }
  .contact-list .icon {
    width: 12px;
    height: 12px;
    flex: none;
  }
  .social-list {
    list-style: none;
    margin: 0;
    padding: 0;
    position: absolute;
    left: 31px;
    top: 270px;
    color: var(--white);
    font-family: "Open Sans", sans-serif;
    font-size: 15px;
  }
  .social-list li {
    display: flex;
    align-items: center;
    gap: 6px;
    height: 27px;
  }
  .social-dot {
    width: 21px;
    height: 21px;
    border-radius: 50%;
    background: var(--white);
    flex: none;
  }
  .brand-mark {
    position: absolute;
    left: 0;
    right: 0;
    top: 86px;
    display: flex;
    flex-direction: column;
    align-items: center;
    gap: 36px;
  }
  .brand-circle {
    width: 84px;
    height: 84px;
    border: 4px solid var(--blush);
    border-radius: 50%;
    box-sizing: border-box;
  }
  .brand-name {
    margin: 0;
    font-family: "Montserrat", sans-serif;
    font-weight: 400;
    font-size: 40px;
    letter-spacing: 18px;
    padding-left: 18px;
    color: var(--blush);
  }
</style>
</head>
<body>
<main class="canvas">

  <section class="card card--founder" aria-label="Founder business card">
    <svg class="founder-panel" width="588" height="364" viewBox="0 0 588 364" aria-hidden="true">
      <polygon points="0,0 418,0 585,292 420,364 0,364" fill="var(--blush)"/>
    </svg>

    <div class="founder-details">
      <h1 class="founder-name">Sunela Parvaniya</h1>
      <p class="founder-title">Founder</p>
      <p class="founder-abn">ABN: 58219740312</p>
    </div>

    <ul class="contact-list">
      <li>
        <svg class="icon" viewBox="0 0 12 12" aria-hidden="true"><path d="M2.5 1 L4.5 1 L5.2 3.5 L4 4.5 Q5 7 7.5 8 L8.5 6.8 L11 7.5 L11 9.5 Q10.5 11 9 11 Q2 10 1 3 Q1 1.5 2.5 1 Z" fill="var(--white)"/></svg>
        <span>+61452913307</span>
      </li>
      <li>
        <svg class="icon" viewBox="0 0 12 12" aria-hidden="true"><rect x="1" y="3" width="10" height="7" fill="var(--white)"/><path d="M1 3 L6 7 L11 3" fill="none" stroke="var(--blush)" stroke-width="1"/></svg>
        <span>sunela@quiremo.com.au</span>
      </li>
      <li>
        <svg class="icon" viewBox="0 0 12 12" aria-hidden="true"><circle cx="6" cy="6" r="5" fill="var(--white)"/><path d="M1 6 H11 M6 1 Q3 6 6 11 Q9 6 6 1" fill="none" stroke="var(--blush)" stroke-width="0.8"/></svg>
        <span>www.quiremo.com.au</span>
      </li>
    </ul>

    <ul class="social-list">
      <li><span class="social-dot" aria-hidden="true"></span><span>@quiremojewellery</span></li>
      <li><span class="social-dot" aria-hidden="true"></span><span>quiremo_jewellery</span></li>
    </ul>
  </section>

  <section class="card card--brand" aria-label="Brand business card">
    <div class="brand-mark">
      <span class="brand-circle" aria-hidden="true"></span>
      <p class="brand-name">QUIREMO</p>
    </div>
  </section>

</main>
</body>
</html>
```